Cocktail-Making Assistant App re-design

Ok boys and girls, here's the deal:
I have an android app which is almost complete, but needs a design overhaul.

The app is a standard cocktail-making assistant: gives you a list of cocktails and the ability to see which cocktail you can make out of those ingredients (drinks, fruit, etc) you have at home.

I've attached some general app flow, as well as detailed requirements/explanation presentation. Most of those things are just FYI, so that you know what it's about.

3 screens are the most important (main screen, cocktail view screen, ingredient view screen), meaning I will pick the design mostly based on ideas for those 3 things, with the fourth being a rather simple list (given on attached flow, third tier)
Some other screens are derived from that, with some minor changes on it, but you shouldn't care about that.

There are lots of other, non-explained things which I said nothing about only because they are (from design point of view) completely the same and would only make it seem more complicated.

I don't want to influence the colour scheme, but the app will be released under RedFig developer name (having a light colured red fig as a logo) so I suppose some brownish design, for example, will not really fit nicely. If you, however, have a killer which you are confident will prove me wrong, I'm looking forward to seeing it!

It should be a serious, elegant look (as opposed to cartoonish, but we are not aiming for a business look at all!), not cluttered with details, no clubbing themes, glitter and so on.

Test apk file available on request (Android 2.3+).

Edit: payment is now guaranteed
Also please note that currently, the favorite, "heart" button has a motion effect:
on click it flies out of the screen to the left (white heart) and comes back to the screen as a red heart. Take that into consideration, if it means anything to you.

Target Market(s)

Whoever you imagine would enjoy drinking cocktails

Industry/Entity Type

Business

Requirements
Must have
• Everything is said in the provided documentation - images say more than I could possibly write here.
Nice to have
• As said, most of the icons are a nice-to-have. Only those which are critically linked to the rest of the design must be provided. More details in the docs.
Should not have
• No cartoon look, No zillion colours

```html
<!DOCTYPE html>
<html lang="en">
<head>
<meta charset="utf-8">
<title>Cocktail Assistant Screens</title>
<link href="https://fonts.googleapis.com/css2?family=Didact+Gothic&display=swap" rel="stylesheet">
<style>
:root{
  --page:#ffffff;
  --night:#1a0c22;
  --plum:#3a1240;
  --magenta:#e0148f;
  --pink:#ff3fae;
  --teal:#0f6a6a;
  --violet:#3b2ba0;
  --text:#ffffff;
  --muted:#cfc6d6;
  --frame:#8e8896;
  --star:#d4d0d8;
}
*{box-sizing:border-box;margin:0;padding:0}
html,body{width:1200px;height:839px;overflow:hidden;background:var(--page)}
body{position:relative;font-family:"Didact Gothic",sans-serif;color:var(--text)}
.screen{
  position:absolute;top:6px;width:440px;height:780px;overflow:hidden;
  background:
    radial-gradient(ellipse 150px 90px at 150px 0,rgba(224,20,143,.75),transparent 70%),
    radial-gradient(ellipse 140px 220px at 10px 330px,rgba(15,106,106,.55),transparent 70%),
    radial-gradient(ellipse 170px 160px at 430px 260px,rgba(59,43,160,.55),transparent 70%),
    radial-gradient(ellipse 200px 120px at 200px 780px,rgba(224,20,143,.55),transparent 70%),
    linear-gradient(180deg,#44123c 0%,var(--night) 30%,#2a0f33 60%,#4a1547 100%);
}
.screen--search{left:24px}
.screen--detail{left:678px}
.screen-title{position:absolute;top:24px;left:0;width:100%;text-align:center;font-size:44px;font-weight:400}
.abs{position:absolute}

/* search screen */
.search-label{left:33px;top:136px;font-size:26px}
.search-field{left:51px;top:179px;width:352px;height:40px;border:2px solid var(--frame);display:flex;align-items:center;justify-content:space-between;padding:0 12px 0 13px}
.search-field span{font-size:16px;color:var(--muted);letter-spacing:.5px}
.search-hint{left:70px;top:236px;width:310px;text-align:center;font-size:15px;line-height:20px;color:#f2eef5}
.category{height:59px;display:flex;align-items:center;background:linear-gradient(90deg,rgba(40,90,170,.8),rgba(60,70,190,.85));box-shadow:0 1px 0 rgba(255,255,255,.08)}
.category svg{position:absolute;left:14px}
.category span{position:absolute;left:121px;font-size:36px}
.category--all{left:41px;top:393px;width:354px;background:linear-gradient(90deg,rgba(20,80,150,.85),rgba(50,90,190,.85))}
.category--cocktails{left:41px;top:472px;width:352px;background:linear-gradient(90deg,rgba(35,55,120,.85),rgba(60,60,190,.85))}
.category--party{left:38px;top:550px;width:354px;background:linear-gradient(90deg,rgba(70,40,110,.85),rgba(70,60,200,.85))}
.nav-back{left:50px;top:727px}
.nav-home{left:160px;top:719px}
.okay{width:138px;height:40px;display:flex;align-items:center;justify-content:center;font-size:22px;background:linear-gradient(90deg,rgba(224,20,143,.7),rgba(120,30,110,.55))}
.screen--search .okay{left:281px;top:721px}
.screen--detail .okay{left:281px;top:721px}

/* detail screen */
.drink-name{left:33px;top:136px;font-size:27px}
.drink-photo{left:259px;top:142px;width:162px;height:174px;border:3px solid #fff;background:linear-gradient(160deg,#3a1545,#2a0f35)}
.drink-info{left:51px;top:194px;width:189px;height:57px;border:2px solid var(--frame);padding:6px 0 0 14px;font-size:15.5px;line-height:21px}
.rating{left:40px;top:267px}
.drink-desc{left:84px;top:331px;width:292px;text-align:center;font-size:15px;line-height:20px}
.ingredient{left:42px;width:353px;height:47px;display:flex;align-items:center}
.ingredient .tick{position:absolute;left:10px}
.ingredient .label{position:absolute;left:50px;font-size:27px}
.ingredient .add{position:absolute;left:307px;width:35px;height:35px;border-radius:4px;background:rgba(210,205,225,.85);display:flex;align-items:center;justify-content:center}
.ing-1{top:427px;background:linear-gradient(90deg,rgba(30,70,140,.85),rgba(60,60,170,.85))}
.ing-2{top:489px;background:linear-gradient(90deg,rgba(40,60,130,.85),rgba(70,60,180,.85))}
.ing-3{top:551px;background:linear-gradient(90deg,rgba(90,40,120,.75),rgba(80,60,180,.8))}
.ing-4{top:613px;background:linear-gradient(90deg,rgba(180,30,130,.75),rgba(150,40,150,.75))}
.ing-5{top:670px;height:30px;opacity:.35;background:linear-gradient(90deg,rgba(200,30,140,.8),rgba(150,40,150,.8))}
.ing-5 .label{font-size:21px}
.ing-5 .add{width:30px;height:22px;left:309px}
</style>
</head>
<body>

<section class="screen screen--search">
  <h1 class="screen-title">Cocktail Search</h1>
  <div class="abs search-label">Search</div>
  <div class="abs search-field">
    <span>Tap here to edit text . . .</span>
    <svg width="30" height="28" viewBox="0 0 30 28" aria-hidden="true"><circle cx="11" cy="11" r="8" fill="none" stroke="#fff" stroke-width="4"/><line x1="17" y1="17" x2="26" y2="25" stroke="#fff" stroke-width="5" stroke-linecap="round"/></svg>
  </div>
  <p class="abs search-hint">You can search the entire collection of all categories or else simply select a subcategory from below list.</p>

  <div class="abs category category--all">
    <svg width="40" height="38" viewBox="0 0 24 23"><path d="M12 0l3.1 7.6 8.2.6-6.3 5.3 2 8-7-4.4-7 4.4 2-8L.7 8.2l8.2-.6z" fill="#fff"/></svg>
    <span>All</span>
  </div>
  <div class="abs category category--cocktails">
    <svg width="40" height="38" viewBox="0 0 24 23"><path d="M12 0l3.1 7.6 8.2.6-6.3 5.3 2 8-7-4.4-7 4.4 2-8L.7 8.2l8.2-.6z" fill="#fff"/></svg>
    <span>Cocktails</span>
  </div>
  <div class="abs category category--party">
    <svg width="40" height="38" viewBox="0 0 24 23"><path d="M12 0l3.1 7.6 8.2.6-6.3 5.3 2 8-7-4.4-7 4.4 2-8L.7 8.2l8.2-.6z" fill="#fff"/></svg>
    <span>Party Drinks</span>
  </div>

  <svg class="abs nav-back" width="42" height="32" viewBox="0 0 42 32" aria-label="Back"><path d="M18 2L4 16l14 14M5 16h35" fill="none" stroke="#d8279a" stroke-width="7" stroke-linejoin="round"/></svg>
  <svg class="abs nav-home" width="46" height="40" viewBox="0 0 46 40" aria-label="Home"><path d="M23 3L3 21h6v17h10V27h8v11h10V21h6z" fill="#ff4fbf"/></svg>
  <div class="abs okay">Okay !</div>
</section>

<section class="screen screen--detail">
  <h1 class="screen-title">App Name</h1>
  <div class="abs drink-name">Harlow Irish Cream</div>
  <div class="abs drink-photo" role="img" aria-label="Photo of the drink"></div>
  <div class="abs drink-info">Type - Sample type<br>Volume - Sample vol</div>
  <svg class="abs rating" width="206" height="44" viewBox="0 0 206 44" aria-label="Rating 2 of 5">
    <defs><path id="star" d="M20 2l5.2 12.6 13.6 1-10.4 8.8 3.3 13.2L20 30.3 8.3 37.6l3.3-13.2L1.2 15.6l13.6-1z"/></defs>
    <use href="#star" x="0" fill="var(--star)"/>
    <use href="#star" x="41" fill="var(--star)"/>
    <use href="#star" x="82" fill="none" stroke="var(--star)" stroke-width="2.5"/>
    <use href="#star" x="123" fill="none" stroke="var(--star)" stroke-width="2.5"/>
    <use href="#star" x="164" fill="none" stroke="var(--star)" stroke-width="2.5"/>
  </svg>
  <p class="abs drink-desc">“Some description which is about 2 sentenc-es can be placed here. Some description which is about 2 sentences can be placed here.”</p>

  <div class="abs ingredient ing-1">
    <svg class="tick" width="26" height="24" viewBox="0 0 26 24"><path d="M2 13l7 8L24 3" fill="none" stroke="#fff" stroke-width="4"/></svg>
    <span class="label">0.5 oz light Rum</span>
    <span class="add"><svg width="26" height="26" viewBox="0 0 26 26"><circle cx="13" cy="13" r="11" fill="none" stroke="#3a2a7a" stroke-width="2.5"/><path d="M13 7v12M7 13h12" stroke="#3a2a7a" stroke-width="3"/></svg></span>
  </div>
  <div class="abs ingredient ing-2">
    <svg class="tick" width="26" height="24" viewBox="0 0 26 24"><path d="M2 13l7 8L24 3" fill="none" stroke="#fff" stroke-width="4"/></svg>
    <span class="label">0.5 oz Coralia Rum</span>
    <span class="add"><svg width="26" height="26" viewBox="0 0 26 26"><circle cx="13" cy="13" r="11" fill="none" stroke="#3a2a7a" stroke-width="2.5"/><path d="M13 7v12M7 13h12" stroke="#3a2a7a" stroke-width="3"/></svg></span>
  </div>
  <div class="abs ingredient ing-3">
    <span class="label">1 oz Sample Rum</span>
    <span class="add"><svg width="26" height="26" viewBox="0 0 26 26"><circle cx="13" cy="13" r="11" fill="none" stroke="#3a2a7a" stroke-width="2.5"/><path d="M13 7v12M7 13h12" stroke="#3a2a7a" stroke-width="3"/></svg></span>
  </div>
  <div class="abs ingredient ing-4">
    <svg class="tick" width="26" height="24" viewBox="0 0 26 24"><path d="M2 13l7 8L24 3" fill="none" stroke="#fff" stroke-width="4"/></svg>
    <span class="label">2 oz Orangelle</span>
  </div>
  <div class="abs ingredient ing-5">
    <svg class="tick" width="22" height="20" viewBox="0 0 26 24"><path d="M2 13l7 8L24 3" fill="none" stroke="#fff" stroke-width="4"/></svg>
    <span class="label">2.5 oz Milk</span>
    <span class="add"><svg width="20" height="20" viewBox="0 0 26 26"><circle cx="13" cy="13" r="11" fill="none" stroke="#3a2a7a" stroke-width="2.5"/><path d="M13 7v12M7 13h12" stroke="#3a2a7a" stroke-width="3"/></svg></span>
  </div>

  <div class="abs okay">Okay !</div>
</section>

</body>
</html>
```